Satchel & Sundial needs new business card design

I need a new business card design. I'm looking for out-of-the-box design which represents the freedom of being a location independent entrepreneur.
I offer coaching, retreats and trips.
I would like to see designs with and without the photo.
Colors I use are black (#000000), green (#25A796) and brown (#D7C38C)
Website satchelandsundial.example

Target Market(s)

location independent entrepreneurs, digital nomads, people looking to swap the 9 to 5 for a lifestyle business

Industry/Entity Type

Business

Contact Information for Business Card

Dorota Falkner
Your Lifestyle Business Coach, Retreat & Trip Leader
http://satchelandsundial.example
hello@satchelandsundial.example
Live a life you don't need a holiday from

Font styles to use
Serif
Sans Serif

Requirements
Must have
• One side should contain only the logo. I would also consider having the "Live a life you don't need a holiday from" on that side too (depending on how it looks)
• Please show both sides on the designs.

```html
<!DOCTYPE html>
<html lang="en">
<head>
<meta charset="utf-8">
<title>Satchel &amp; Sundial – Business Card</title>
<link rel="stylesheet" href="https://fonts.googleapis.com/css2?family=Open+Sans:wght@400;600;700&display=swap">
<style>
  :root {
    --ink: #1d1b17;
    --teal: #25a796;
    --card: #d9c590;
    --backdrop: #e9e6e0;
    --edge: #c4b07c;
  }
  * { box-sizing: border-box; margin: 0; padding: 0; }
  html, body {
    width: 1200px; height: 900px; overflow: hidden;
    background: var(--backdrop);
    font-family: "Open Sans", Arial, sans-serif;
    color: var(--ink);
  }
  .canvas {
    position: relative; width: 1200px; height: 900px;
  }
  .card {
    position: absolute;
    width: 700px; height: 400px;
    background: var(--card);
    border-radius: 4px;
    box-shadow: 0 10px 28px rgba(0,0,0,0.18), 0 1px 0 var(--edge);
  }
  .card--front { left: 250px; top: 40px; }
  .card--back  { left: 250px; top: 460px; }

  .wordmark {
    font-weight: 700;
    text-transform: uppercase;
    letter-spacing: 0.04em;
    color: var(--ink);
    white-space: nowrap;
  }
  .card--front .wordmark {
    position: absolute; left: 0; right: 0; top: 160px;
    text-align: center; font-size: 46px;
  }

  .card--back .wordmark {
    position: absolute; right: 36px; top: 80px;
    font-size: 30px;
  }
  .holder {
    position: absolute; left: 50px; top: 60px;
  }
  .holder__name {
    color: var(--teal); font-weight: 700; font-size: 22px; line-height: 1.2;
  }
  .holder__role {
    font-weight: 600; font-size: 15px; line-height: 1.5; margin-top: 4px;
  }
  .contact {
    position: absolute; left: 50px; top: 262px;
    list-style: none; font-size: 16px; line-height: 1.6;
  }
  .contact__item { display: flex; align-items: center; gap: 12px; }
  .contact__icon { width: 14px; height: 14px; flex: none; }
  .tagline {
    position: absolute; left: 50px; right: 36px; bottom: 38px;
    font-weight: 700; font-size: 19px; letter-spacing: 0.16em;
    text-transform: uppercase;
  }
</style>
</head>
<body>
<main class="canvas">
  <section class="card card--front" aria-label="Card front">
    <p class="wordmark">Satchel &amp; Sundial</p>
  </section>

  <section class="card card--back" aria-label="Card back">
    <div class="holder">
      <p class="holder__name">Dorota Falkner</p>
      <p class="holder__role">Your Lifestyle Business Coach,<br>Retreat &amp; Trip Leader</p>
    </div>
    <p class="wordmark">Satchel &amp; Sundial</p>
    <ul class="contact">
      <li class="contact__item">
        <svg class="contact__icon" viewBox="0 0 14 14" aria-hidden="true">
          <rect x="0" y="2" width="14" height="10" fill="var(--teal)"/>
          <path d="M0 2 L7 8 L14 2" fill="none" stroke="var(--card)" stroke-width="1.3"/>
        </svg>
        hello@satchelandsundial.example
      </li>
      <li class="contact__item">
        <svg class="contact__icon" viewBox="0 0 14 14" aria-hidden="true">
          <circle cx="7" cy="7" r="7" fill="var(--teal)"/>
          <path d="M3.5 7.2 L6 9.5 L10.5 4.5" fill="none" stroke="var(--card)" stroke-width="1.6"/>
        </svg>
        www.satchelandsundial.example
      </li>
    </ul>
    <p class="tagline">Live a life you don't need a holiday from</p>
  </section>
</main>
</body>
</html>
```